Craft brewery keg badge / badge branding to be on display on keg fonts in pubs and craft beer bars

We're a small craft beer producer and are looking to have a keg badge designed to be put onto keg fonts in bars as well as being used on our bottles. Our website is www.qelnoriales.co.uk. -Please take a look at our site however we're looking for new branding! We're not looking to have the windmill on the badge! We want a bold geometric hop design in the centre of the design. The beer is a low AVB beer (2.9% ABV) and will be hopped with Cascade, Colombus and Tarvel hops and will have a fruity / juicy aroma. We're looking to have a design that we can re-use again and again by changing: colours and wording for different beers in the future.

Target Market(s)
Craft beer drinkers
Industry/Entity Type
Craft Brewery
Requirements
Must have
- Simple, elegant, repeatable core message from the badge. It need a simple, bold geometric hop design (examples uploaded) in the centre which is repeatable across many brands in the future.
- The badge needs to be circular and 82mm across to fit our tap lenses (see http://www.vindex.co.uk/branding for the flat lens). The keg badge needs to be modern and in line with other keg badges like the examples attached- though we leave the artistic flair up to you guys. Please see below the styles of keg badge we like.
- Must be in vector file format and we must get a jpeg version too.

Should not have
- Should not be overcrowded and try to be too full of information. See attached examples.

```html
<!DOCTYPE html>
<html lang="en">
<head>
<meta charset="utf-8">
<title>Craft Brewery Keg Badge</title>
<link href="https://fonts.googleapis.com/css2?family=Oswald:wght@600&display=swap" rel="stylesheet">
<style>
  :root {
    --badge-red: #7b1517;
    --page-bg: #ffffff;
    --barrel-rim: #8a3d1a;
    --barrel-light: #b35d25;
    --barrel-dark: #6e2c12;
    --cream: #ecdcaf;
    --gold: #f4c95d;
    --wheat-light: #f3c96a;
    --wheat-dark: #d9952e;
  }
  html, body {
    margin: 0;
    padding: 0;
    width: 1200px;
    height: 1200px;
    overflow: hidden;
    background: var(--page-bg);
  }
  .badge {
    display: block;
    width: 1200px;
    height: 1200px;
  }
  .badge-text {
    font-family: "Oswald", "Arial Narrow", sans-serif;
    font-weight: 600;
    fill: var(--cream);
  }
  .website { font-size: 72px; }
  .title-craft { font-size: 122px; }
  .title-brewery { font-size: 200px; }
  .since-label { font-size: 36px; }
  .strength { font-size: 64px; fill: var(--gold); }
  .rule { stroke: var(--cream); stroke-width: 3; }
  .star { fill: var(--cream); }
</style>
</head>
<body>
<svg class="badge" viewBox="0 0 1200 1200" xmlns="http://www.w3.org/2000/svg">
  <defs>
    <radialGradient id="barrelFill" cx="50%" cy="50%" r="50%">
      <stop offset="0%" stop-color="var(--barrel-light)"/>
      <stop offset="100%" stop-color="var(--barrel-dark)"/>
    </radialGradient>
    <linearGradient id="wheatFill" x1="0" y1="0" x2="0" y2="1">
      <stop offset="0%" stop-color="var(--wheat-light)"/>
      <stop offset="100%" stop-color="var(--wheat-dark)"/>
    </linearGradient>
    <path id="websiteArc" d="M 145 600 A 455 455 0 0 1 1055 600"/>
  </defs>

  <circle class="badge-disc" cx="600" cy="600" r="590" fill="var(--badge-red)"/>

  <g class="barrel-end" role="img" aria-label="Illustrated wooden barrel end with plank grain">
    <circle cx="600" cy="612" r="418" fill="var(--barrel-rim)"/>
    <circle cx="600" cy="612" r="378" fill="url(#barrelFill)"/>
  </g>

  <ellipse class="wheat-left" role="img" aria-label="Illustrated golden wheat ear" cx="112" cy="640" rx="34" ry="280" fill="url(#wheatFill)" transform="rotate(-10 112 640)"/>
  <ellipse class="wheat-right" role="img" aria-label="Illustrated golden wheat ear" cx="1088" cy="640" rx="34" ry="280" fill="url(#wheatFill)" transform="rotate(10 1088 640)"/>

  <text class="badge-text website" text-anchor="middle">
    <textPath href="#websiteArc" startOffset="50%" textLength="640" lengthAdjust="spacing">QELNORIALES.CO.UK</textPath>
  </text>
  <circle class="star" cx="262" cy="210" r="7"/>
  <circle class="star" cx="938" cy="210" r="7"/>

  <text class="badge-text title-craft" x="606" y="420" text-anchor="middle" textLength="335" lengthAdjust="spacing">CRAFT</text>

  <rect class="mug-emblem" role="img" aria-label="Illustrated beer mug with foam and a geometric hop cone" x="512" y="482" width="220" height="236" rx="14" fill="var(--gold)"/>

  <g class="since-mark">
    <line class="rule" x1="265" y1="580" x2="372" y2="580"/>
    <text class="badge-text since-label" x="318" y="620" text-anchor="middle" textLength="88" lengthAdjust="spacing">SINCE</text>
    <line class="rule" x1="265" y1="628" x2="372" y2="628"/>
    <line class="rule" x1="845" y1="580" x2="952" y2="580"/>
    <text class="badge-text since-label" x="898" y="620" text-anchor="middle" textLength="84" lengthAdjust="spacing">1930</text>
    <line class="rule" x1="845" y1="628" x2="952" y2="628"/>
  </g>

  <text class="badge-text title-brewery" x="602" y="940" text-anchor="middle" textLength="850" lengthAdjust="spacingAndGlyphs">BREWERY</text>

  <text class="badge-text strength" x="603" y="1128" text-anchor="middle" textLength="284" lengthAdjust="spacing">2.9% RBV</text>
</svg>
</body>
</html>
```